Bry7Legal Letterhead

Need a new letterhead for my law firm.
IDENTIFYING INFORMATION BELOW:
Anselmo R Quintara III
Attorney at Law
Address: 2847 Larkspur Blvd, Ste 300, Dallas, TX 75204
Phone: 877-482-6017
Fax: 469-738-1452
Email: bry@bry7legal.example
Website: www.bry7legal.example

Colors
0054AA
0677BA
7BADD7
CADEEF
E8F1F8

Requirements
Must have
• Logo needs to be on the letterhead, along with identifying information which is included in the project description.

```html
<!DOCTYPE html>
<html lang="en">
<head>
<meta charset="utf-8">
<title>Bry7Legal Letterhead</title>
<link href="https://fonts.googleapis.com/css2?family=Montserrat:wght@300;400;600;700&family=Open+Sans:wght@400;600&display=swap" rel="stylesheet">
<style>
  :root {
    --ink: #1b1b1b;
    --heading: #2e2e2e;
    --body-grey: #858585;
    --meta-grey: #7a7a7a;
    --blue-deep: #0054AA;
    --blue-mid: #0677BA;
    --blue-bright: #2aa3dd;
    --blue-soft: #CADEEF;
    --blue-pale: #E8F1F8;
    --paper: #ffffff;
    --backdrop: #dcdcdc;
  }
  * { margin: 0; padding: 0; box-sizing: border-box; }
  html, body { width: 1096px; height: 1200px; overflow: hidden; background: var(--backdrop); }
  .letterhead {
    position: absolute; left: 124px; top: 0; width: 848px; height: 1200px;
    background: var(--paper); font-family: "Open Sans", sans-serif;
  }
  .letterhead__shapes { position: absolute; inset: 0; width: 848px; height: 1200px; }
  .brand { position: absolute; left: 69px; top: 46px; width: 304px; text-align: center; }
  .brand__name {
    font-family: "Montserrat", sans-serif; font-weight: 700; font-size: 42px;
    letter-spacing: 1px; color: var(--ink); line-height: 1;
  }
  .brand__tagline {
    font-family: "Montserrat", sans-serif; font-weight: 300; font-size: 17px;
    letter-spacing: 2.6px; color: var(--ink); margin-top: 6px; text-transform: uppercase;
  }
  .attorney { position: absolute; right: 72px; top: 56px; text-align: right; font-family: "Montserrat", sans-serif; }
  .attorney__name { font-weight: 600; font-size: 16px; color: var(--heading); text-transform: uppercase; }
  .attorney__title { font-weight: 400; font-size: 10.5px; color: var(--heading); text-transform: uppercase; margin-top: 3px; }
  .recipient { position: absolute; left: 72px; top: 310px; }
  .recipient__name { font-weight: 600; font-size: 19px; color: var(--heading); margin-bottom: 7px; }
  .recipient__line { font-size: 11.5px; color: var(--meta-grey); line-height: 18.4px; }
  .letter-date { position: absolute; right: 101px; top: 396px; font-size: 11.5px; color: var(--ink); }
  .letter-body { position: absolute; left: 70px; width: 706px; top: 452px; }
  .letter-body p {
    font-size: 11.6px; line-height: 18.3px; color: var(--body-grey);
    text-align: justify; margin-bottom: 18px;
  }
  .signature {
    position: absolute; left: 96px; top: 813px; width: 199px; height: 40px;
    background: linear-gradient(90deg, #efefef, #f6f6f6); border-radius: 4px;
  }
  .contact-row {
    position: absolute; left: 71px; right: 72px; top: 1083px;
    display: flex; justify-content: space-between; align-items: center;
  }
  .contact-item { display: flex; align-items: center; gap: 9px; font-size: 11px; color: var(--heading); }
  .contact-item__icon {
    width: 26px; height: 26px; display: flex; align-items: center; justify-content: center;
    background: linear-gradient(135deg, var(--blue-bright), var(--blue-mid));
  }
  .contact-item__icon svg { width: 15px; height: 15px; }
  .website {
    position: absolute; right: 72px; top: 1145px;
    font-weight: 600; font-size: 12.5px; color: var(--blue-mid);
  }
</style>
</head>
<body>
<main class="letterhead">
  <svg class="letterhead__shapes" viewBox="0 0 1173 1660" preserveAspectRatio="none" aria-hidden="true">
    <defs>
      <linearGradient id="band-header" x1="0" x2="1" y1="0" y2="0">
        <stop offset="0" stop-color="#1c5fa6"/>
        <stop offset="1" stop-color="#2aa3dd"/>
      </linearGradient>
      <linearGradient id="band-footer" x1="0" x2="1" y1="0" y2="0">
        <stop offset="0" stop-color="#2aa3dd"/>
        <stop offset="1" stop-color="#1c5fa6"/>
      </linearGradient>
    </defs>
    <!-- header -->
    <polygon points="0,192 600,192 592,201 0,201" fill="#1b1b1b"/>
    <polygon points="668,148 688,148 630,201 610,201" fill="#1f8fd4"/>
    <polygon points="708,148 1173,148 1173,201 650,201" fill="url(#band-header)"/>
    <!-- footer -->
    <polygon points="0,1557 838,1557 781,1610 0,1610" fill="url(#band-footer)"/>
    <polygon points="856,1557 878,1557 821,1610 801,1610" fill="#1f8fd4"/>
    <polygon points="899,1557 1173,1557 1173,1565 891,1565" fill="#1b1b1b"/>
  </svg>

  <header>
    <div class="brand">
      <div class="brand__name">BRY7LEGAL</div>
      <div class="brand__tagline">Counsel That Moves</div>
    </div>
    <div class="attorney">
      <div class="attorney__name">Anselmo R Quintara III</div>
      <div class="attorney__title">Attorney at Law</div>
    </div>
  </header>

  <section class="recipient">
    <div class="recipient__name">Name Surname</div>
    <div class="recipient__line">Attorney at Law</div>
    <div class="recipient__line">Address goes here. Street, City, Country</div>
    <div class="recipient__line">contact@yourmail.com</div>
    <div class="recipient__line">000-987-654-321</div>
  </section>
  <div class="letter-date">Date, 10 September, 2030</div>

  <section class="letter-body">
    <p>Lorem ipsum dolor sit amet, consectetur adipisicing elit, sed do eiusmod tempor incididunt ut labore et dolore magna aliqua. Ut enim ad minim veniam, quis nostrud exercitation ullamco laboris nisi ut aliquip ex ea commodo consequat. Duis aute irure dolor in reprehenderit in voluptate velit esse cillum dolore eu fugiat nulla pariatur. Excepteur sint occaecat cupidatat non proident, sunt in culpa qui officia deserunt mollit anim id est laborum. Sed ut perspiciatis unde omnis iste natus error sit voluptatem accusantium doloremque laudantium, totam rem aperiam, eaque ipsa quae ab illo inventore veritatis et quasi architecto beatae vitae dicta sunt explicabo. Nemo enim ipsam voluptatem quia voluptas sit aspernatur aut odit aut fugit, sed quia consequuntur magni dolores eos qui ratione voluptatem sequi nesciunt. Neque porro voluptatem sequi nesciunt. Nemo enim ipsam voluptatem quia voluptas.</p>
    <p>Lorem ipsum dolor sit amet, consectetur adipisicing elit, sed do eiusmod tempor incididunt ut labore et dolore magna aliqua. Ut enim ad minim veniam, quis nostrud exercitation ullamco laboris nisi ut aliquip ex ea commodo consequat. Duis aute irure dolor in reprehenderit in voluptate velit esse cillum dolore eu fugiat nulla pariatur. Excepteur sint occaecat cupidatat non proident, sunt in culpa qui officia deserunt mollit anim id est laborum. Sed ut perspiciatis unde omnis iste natus error sit voluptatem accusantium doloremque laudantium, totam rem aperiam, eaque ipsa quae ab illo inventore veritatis et quasi architecto beatae vitae dicta sunt explicabo. Nemo enim ipsam voluptatem quia voluptas sit aspernatur aut odit aut.</p>
    <p>Lorem ipsum dolor sit amet, consectetur adipisicing elit, sed do eiusmod tempor incididunt ut labore et dolore magna aliqua. Ut enim ad minim veniam, quis nostrud exercitation ullamco laboris nisi ut aliquip ex ea commodo consequat. .</p>
  </section>

  <div class="signature" role="img" aria-label="Handwritten signature of the sender"></div>

  <footer>
    <div class="contact-row">
      <div class="contact-item">
        <span class="contact-item__icon"><svg viewBox="0 0 16 16"><path d="M2 6c0-2 2-3 6-3s6 1 6 3v1h-3V5.5H5V7H2z M4 8h8l1 5H3z" fill="#fff"/></svg></span>
        <span>877-482-6017</span>
      </div>
      <div class="contact-item">
        <span class="contact-item__icon"><svg viewBox="0 0 16 16"><rect x="4.5" y="2" width="7" height="4" fill="#fff"/><rect x="2" y="6" width="12" height="5" rx="1" fill="#fff"/><rect x="4.5" y="10" width="7" height="4" fill="#fff" stroke="#1f8fd4" stroke-width="0.8"/></svg></span>
        <span>469-738-1452</span>
      </div>
      <div class="contact-item">
        <span class="contact-item__icon"><svg viewBox="0 0 16 16"><rect x="2" y="4" width="12" height="8" fill="none" stroke="#fff" stroke-width="1.2"/><path d="M2 4l6 5 6-5" fill="none" stroke="#fff" stroke-width="1.2"/></svg></span>
        <span>bry@bry7legal.example</span>
      </div>
      <div class="contact-item">
        <span class="contact-item__icon"><svg viewBox="0 0 16 16"><path d="M8 1.5a4.5 4.5 0 0 1 4.5 4.5c0 3.3-4.5 8.5-4.5 8.5S3.5 9.3 3.5 6A4.5 4.5 0 0 1 8 1.5z" fill="#fff"/><circle cx="8" cy="6" r="1.7" fill="#1f8fd4"/></svg></span>
        <span>2847 Larkspur Blvd, Ste 300, Dallas, TX 75204</span>
      </div>
    </div>
    <div class="website">www.bry7legal.example</div>
  </footer>
</main>
</body>
</html>
```